Business Card Design

We need a business card designed for our new company. Prefer a black card with white logo & writing.

Contact Information for Business Card

Ted Galloway, address: 7-4812 Fernhollow Road, Abbotsford, BC, V3K 8R2, Office Phone: 604-712-3390, Cell: 604-947-2164, Email: ted@resinworkshub.ca

Colors

Designer to choose only greyscale colors for use in the design.

```html
<!DOCTYPE html>
<html lang="en">
<head>
<meta charset="UTF-8">
<title>Resin Works Hub – Business Card</title>
<link href="https://fonts.googleapis.com/css2?family=Poppins:wght@300;400;600;800&display=swap" rel="stylesheet">
<style>
  :root {
    --backdrop: #2a2a2c;
    --card: #1e1e20;
    --ink: #ffffff;
    --ink-soft: #d9d9d9;
  }
  * { margin: 0; padding: 0; box-sizing: border-box; }
  html, body { width: 1200px; height: 780px; overflow: hidden; }
  body {
    background: var(--backdrop);
    font-family: "Poppins", sans-serif;
    color: var(--ink);
    position: relative;
  }
  .card {
    position: absolute;
    top: 236px;
    width: 540px;
    height: 308px;
    background: var(--card);
    border-radius: 4px;
  }
  .card--back { left: 40px; }
  .card--front { left: 620px; }

  .holder {
    position: absolute;
    left: 30px;
    top: 26px;
    padding-left: 12px;
    border-left: 5px solid var(--ink);
    line-height: 1.05;
  }
  .holder__name { font-size: 28px; font-weight: 300; letter-spacing: 0.3px; }
  .holder__name strong { font-weight: 800; }
  .holder__title { font-size: 12px; font-weight: 300; color: var(--ink-soft); margin-top: 2px; }

  .address {
    position: absolute;
    left: 30px;
    top: 128px;
    font-size: 12.5px;
    font-weight: 300;
    line-height: 1.45;
    color: var(--ink-soft);
  }

  .brand {
    position: absolute;
    display: flex;
    align-items: center;
    gap: 10px;
    font-weight: 800;
    color: var(--ink);
    text-transform: uppercase;
    letter-spacing: 1px;
    white-space: nowrap;
  }
  .brand__dot { border-radius: 50%; background: var(--ink); flex: none; }
  .card--back .brand { right: 34px; top: 112px; font-size: 22px; }
  .card--back .brand__dot { width: 16px; height: 16px; }
  .card--front .brand { left: 50%; top: 50%; transform: translate(-50%, -50%); font-size: 38px; gap: 14px; }
  .card--front .brand__dot { width: 26px; height: 26px; }

  .contacts {
    position: absolute;
    right: 30px;
    bottom: 22px;
    list-style: none;
    text-align: right;
    font-size: 13px;
    font-weight: 300;
    line-height: 1.55;
  }
  .contacts li { display: flex; align-items: center; justify-content: flex-end; gap: 10px; }
  .contacts svg { width: 14px; height: 14px; fill: var(--ink); flex: none; }
</style>
</head>
<body>
  <section class="card card--back" aria-label="Card back with contact details">
    <div class="holder">
      <div class="holder__name"><strong>Ted</strong> Galloway</div>
      <div class="holder__title">Founder &amp; CEO</div>
    </div>
    <p class="address">7-4812 Fernhollow Road,<br>Abbotsford, BC, V3K 8R2.</p>
    <div class="brand"><span class="brand__dot"></span>Resin Works Hub</div>
    <ul class="contacts">
      <li>604-712-3390
        <svg viewBox="0 0 24 24" aria-hidden="true"><path d="M6.6 10.8a15 15 0 0 0 6.6 6.6l2.2-2.2a1 1 0 0 1 1-.25 11.4 11.4 0 0 0 3.6.57 1 1 0 0 1 1 1V20a1 1 0 0 1-1 1A17 17 0 0 1 3 4a1 1 0 0 1 1-1h3.5a1 1 0 0 1 1 1c0 1.25.2 2.45.57 3.57a1 1 0 0 1-.25 1z"/></svg>
      </li>
      <li>604-947-2164
        <svg viewBox="0 0 24 24" aria-hidden="true"><path d="M7 1h10a2 2 0 0 1 2 2v18a2 2 0 0 1-2 2H7a2 2 0 0 1-2-2V3a2 2 0 0 1 2-2zm0 3v14h10V4zm5 15.5a1.2 1.2 0 1 0 0 2.4 1.2 1.2 0 0 0 0-2.4z"/></svg>
      </li>
      <li>www.resinworkshub.ca
        <svg viewBox="0 0 24 24" aria-hidden="true"><path d="M12 2a10 10 0 1 0 0 20 10 10 0 0 0 0-20zm6.9 6h-3a15 15 0 0 0-1.3-3.9A8 8 0 0 1 18.9 8zM12 4c.8 1.2 1.5 2.5 1.9 4h-3.8c.4-1.5 1.1-2.8 1.9-4zM4.3 14a8 8 0 0 1 0-4h3.4a16 16 0 0 0 0 4zm.8 2h3a15 15 0 0 0 1.3 3.9A8 8 0 0 1 5.1 16zm3-8h-3a8 8 0 0 1 4.3-3.9A15 15 0 0 0 8.1 8zM12 20c-.8-1.2-1.5-2.5-1.9-4h3.8c-.4 1.5-1.1 2.8-1.9 4zm2.3-6H9.7a14 14 0 0 1 0-4h4.6a14 14 0 0 1 0 4zm.3 5.9a15 15 0 0 0 1.3-3.9h3a8 8 0 0 1-4.3 3.9zm1.7-5.9a16 16 0 0 0 0-4h3.4a8 8 0 0 1 0 4z"/></svg>
      </li>
      <li>ted@resinworkshub.ca
        <svg viewBox="0 0 24 24" aria-hidden="true"><path d="M3 5h18a1 1 0 0 1 1 1v12a1 1 0 0 1-1 1H3a1 1 0 0 1-1-1V6a1 1 0 0 1 1-1zm1 2.3V17h16V7.3l-8 5.2z M5.2 7 12 11.4 18.8 7z"/></svg>
      </li>
    </ul>
  </section>

  <section class="card card--front" aria-label="Card front with company name">
    <div class="brand"><span class="brand__dot"></span>Resin Works Hub</div>
  </section>
</body>
</html>
```